Brindle Asset Management Vendor Recruiting Email

We need a digital flyer to email and post on Social media to attract new vendors to our website to apply to complete maintenance work on our clients homes. I have one flyer we had produced recently that we are un-happy with. It is attached.

The example given is what we do not want!! We do not want any of the pictures used from the existing one

Target Market(s)

Construction companies and handyman

Industry/Entity Type

Residential maintenance and repairs

Requirements
Must have
• Join our team as the header not become a vendor

```html
<!DOCTYPE html>
<html lang="en">
<head>
<meta charset="utf-8">
<title>Brindle Asset Management – Join Our Team</title>
<link rel="stylesheet" href="https://fonts.googleapis.com/css2?family=Anton&family=Montserrat:wght@600;800&display=swap">
<style>
  :root {
    --page: #ecebea;
    --navy: #0e1f33;
    --orange: #f08a0c;
    --lime: #c8d400;
    --lime-shade: #7f8700;
    --white: #ffffff;
    --photo-light: #eef0f1;
    --photo-mid: #c9ccce;
  }
  html, body {
    margin: 0;
    width: 1200px;
    height: 900px;
    overflow: hidden;
    background: var(--page);
  }
  .flyer {
    position: absolute;
    left: 256px;
    top: 20px;
    width: 688px;
    height: 860px;
    display: block;
  }
  .display { font-family: "Anton", "Arial Narrow", sans-serif; }
  .brand-name, .brand-sub, .phone-number { font-family: "Montserrat", Arial, sans-serif; }
  .brand-name { font-weight: 600; font-size: 36px; letter-spacing: 4px; fill: var(--white); }
  .brand-sub { font-weight: 600; font-size: 12px; letter-spacing: 2px; fill: var(--white); }
  .headline { font-size: 150px; fill: var(--lime); }
  .headline-shade { font-size: 150px; fill: var(--lime-shade); }
  .benefit { font-size: 40px; fill: var(--white); }
  .bullet-mark { font-size: 38px; fill: var(--lime); }
  .subhead { fill: var(--lime); }
  .subhead-shade { fill: var(--lime-shade); }
  .requirement { font-size: 40px; fill: var(--white); }
  .cta-label { font-size: 54px; fill: var(--navy); }
  .website { font-size: 96px; fill: var(--lime); }
  .phone-number { font-weight: 800; font-size: 64px; fill: var(--white); }
</style>
</head>
<body>
<svg class="flyer" viewBox="0 0 1147 1435" xmlns="http://www.w3.org/2000/svg">
  <defs>
    <linearGradient id="photo-tone" x1="0" y1="0" x2="1" y2="1">
      <stop offset="0" stop-color="var(--photo-light)"/>
      <stop offset="1" stop-color="var(--photo-mid)"/>
    </linearGradient>
  </defs>

  <rect class="flyer-bg" width="1147" height="1435" fill="var(--navy)"/>

  <polygon class="top-band" points="228,0 922,0 282,150" fill="var(--orange)"/>
  <polygon class="top-rule" points="0,218 282,148 282,156 0,228" fill="var(--orange)"/>

  <g class="brand">
    <rect x="103" y="42" width="28" height="28" fill="var(--white)"/>
    <text class="brand-name" x="118" y="132" text-anchor="middle">BRINDLE</text>
    <text class="brand-sub" x="118" y="152" text-anchor="middle">ASSET MANAGEMENT</text>
  </g>

  <polygon class="photo-frame" points="608,373 1147,232 1147,780 825,868" fill="var(--orange)"/>
  <polygon class="photo" role="img" aria-label="Photo of hands drafting a house plan with a ruler and pencil"
           points="624,381 1147,244 1147,762 835,850" fill="url(#photo-tone)"/>

  <!-- headline -->
  <g transform="translate(85,352) rotate(-13.5) skewX(-6)">
    <text class="display headline-shade" x="6" y="8" textLength="740" lengthAdjust="spacingAndGlyphs">JOIN OUR TEAM</text>
    <text class="display headline" x="0" y="0" textLength="740" lengthAdjust="spacingAndGlyphs">JOIN OUR TEAM</text>
  </g>

  <!-- benefits -->
  <g class="benefits">
    <g transform="translate(80,428) rotate(-13) skewX(-6)"><text class="display bullet-mark">»</text></g>
    <g transform="translate(120,424) rotate(-13.5) skewX(-6)"><text class="display benefit" textLength="690" lengthAdjust="spacingAndGlyphs">95% APPROVAL RATING ON ALL SUBMITTED ESTIMATES.</text></g>
    <g transform="translate(120,473) rotate(-13) skewX(-6)"><text class="display benefit" textLength="365" lengthAdjust="spacingAndGlyphs">GUARANTEED WORK VOLUME.</text></g>

    <g transform="translate(80,540) rotate(-13) skewX(-6)"><text class="display bullet-mark">»</text></g>
    <g transform="translate(120,538) rotate(-13) skewX(-6)"><text class="display benefit" textLength="420" lengthAdjust="spacingAndGlyphs">MATERIAL PURCHASING PROGRAM</text></g>
    <g transform="translate(120,593) rotate(-13) skewX(-6)"><text class="display benefit" textLength="475" lengthAdjust="spacingAndGlyphs">TO HELP VENDORS WITH LOW CAPITAL</text></g>
    <g transform="translate(120,638) rotate(-13) skewX(-6)"><text class="display benefit" textLength="275" lengthAdjust="spacingAndGlyphs">OR NO OR BAD CREDIT.</text></g>

    <g transform="translate(80,706) rotate(-13) skewX(-6)"><text class="display bullet-mark">»</text></g>
    <g transform="translate(120,703) rotate(-13) skewX(-6)"><text class="display benefit" textLength="410" lengthAdjust="spacingAndGlyphs">WEEKLY SECURE DIRECT DEPOSIT</text></g>
    <g transform="translate(120,753) rotate(-13) skewX(-6)"><text class="display benefit" textLength="385" lengthAdjust="spacingAndGlyphs">WITH NET 30 PAYMENT TERMS.</text></g>
  </g>

  <!-- requirements heading -->
  <g transform="translate(88,900) rotate(-12.5) skewX(-6)">
    <text class="display subhead-shade" x="5" y="6" font-size="108" textLength="465" lengthAdjust="spacingAndGlyphs">REQUIREMENTS</text>
    <text class="display subhead" font-size="108" textLength="465" lengthAdjust="spacingAndGlyphs">REQUIREMENTS</text>
  </g>
  <g transform="translate(90,988) rotate(-12.5) skewX(-6)">
    <text class="display subhead-shade" x="4" y="5" font-size="84" textLength="470" lengthAdjust="spacingAndGlyphs">TO BECOME A VENDOR</text>
    <text class="display subhead" font-size="84" textLength="470" lengthAdjust="spacingAndGlyphs">TO BECOME A VENDOR</text>
  </g>

  <!-- requirement list -->
  <g class="requirements">
    <g transform="translate(80,1060) rotate(-12) skewX(-6)"><text class="display bullet-mark">»</text></g>
    <g transform="translate(120,1058) rotate(-12) skewX(-6)"><text class="display requirement" textLength="215" lengthAdjust="spacingAndGlyphs">AUTO INSURANCE</text></g>
    <g transform="translate(80,1106) rotate(-12) skewX(-6)"><text class="display bullet-mark">»</text></g>
    <g transform="translate(120,1103) rotate(-12) skewX(-6)"><text class="display requirement" textLength="580" lengthAdjust="spacingAndGlyphs">CERTIFICATE OF GENERAL LIABILITY INSURANCE</text></g>
    <g transform="translate(80,1151) rotate(-12) skewX(-6)"><text class="display bullet-mark">»</text></g>
    <g transform="translate(120,1148) rotate(-12) skewX(-6)"><text class="display requirement" textLength="820" lengthAdjust="spacingAndGlyphs">WORKMAN'S COMPENSATION OR STATE ISSUED EXEMPTION LETTER</text></g>
    <g transform="translate(80,1201) rotate(-12) skewX(-6)"><text class="display bullet-mark">»</text></g>
    <g transform="translate(120,1198) rotate(-12) skewX(-6)"><text class="display requirement" textLength="495" lengthAdjust="spacingAndGlyphs">DRIVE LICENSE OR STATE ISSUED ID CARD</text></g>
    <g transform="translate(80,1246) rotate(-12) skewX(-6)"><text class="display bullet-mark">»</text></g>
    <g transform="translate(120,1243) rotate(-12) skewX(-6)"><text class="display requirement" textLength="200" lengthAdjust="spacingAndGlyphs">COVERAGE AREA</text></g>
    <g transform="translate(80,1296) rotate(-12) skewX(-6)"><text class="display bullet-mark">»</text></g>
    <g transform="translate(120,1293) rotate(-12) skewX(-6)"><text class="display requirement" textLength="320" lengthAdjust="spacingAndGlyphs">ANY SPECIALTY LICENSES</text></g>
  </g>

  <!-- contact button -->
  <g class="cta" transform="translate(888,1072) rotate(-12)">
    <rect x="-172" y="-46" width="344" height="92" rx="46" fill="var(--lime)"/>
    <circle cx="-124" cy="0" r="32" fill="var(--navy)"/>
    <path d="M-124,-16 V14 M-136,3 L-124,15 L-112,3" stroke="var(--white)" stroke-width="5" fill="none" stroke-linecap="round" stroke-linejoin="round"/>
    <text class="display cta-label" x="-70" y="20" textLength="215" lengthAdjust="spacingAndGlyphs" transform="skewX(-6)">Contact Us</text>
  </g>

  <!-- website -->
  <g transform="translate(128,1408) rotate(-11) skewX(-6)">
    <text class="display website" textLength="950" lengthAdjust="spacingAndGlyphs">WWW.BRINDLEASSETMANAGEMENT.COM</text>
  </g>

  <!-- bottom band -->
  <polygon class="bottom-rule" points="580,1352 1147,1220 1147,1230 582,1362" fill="var(--orange)"/>
  <polygon class="bottom-band" points="268,1435 582,1358 632,1435" fill="var(--orange)"/>

  <!-- phone -->
  <g class="phone">
    <path d="M680,1360 c-6,4 -8,12 -3,22 c8,16 20,28 36,36 c10,5 18,3 22,-3 l4,-6 c2,-3 1,-7 -2,-9 l-10,-7 c-3,-2 -7,-1 -9,1 l-4,5 c-10,-5 -17,-12 -22,-22 l5,-4 c2,-2 3,-6 1,-9 l-7,-10 c-2,-3 -6,-4 -9,-2 z" fill="var(--white)"/>
    <text class="phone-number" x="742" y="1406" textLength="380" lengthAdjust="spacingAndGlyphs">555-013-472</text>
  </g>
</svg>
</body>
</html>
```